business card

Business card for new business.
Red and black corporate colors.
Card can have an Indsutrial feel to it. Feel free to add Rust, Bolted steel, or graphics as you see fit. We provide highly specialized services to the below mentioned industries.
Keep information out of corners so that if I want I can choose rounded corners.
Information
- front. name - title - phone - email
- Rear
Refining - Rail - Infrastructure - Mining - Energy
Calgary - Edmonton - Fort McMurray - Revelstoke - Vancouver

```html
<!DOCTYPE html>
<html lang="en">
<head>
<meta charset="utf-8">
<title>Ironspan Business Card</title>
<link rel="stylesheet" href="https://fonts.googleapis.com/css2?family=Roboto:wght@400;500;700&display=swap">
<style>
  :root {
    --backdrop: #e6e4e1;
    --card: #f7f7f7;
    --red: #e3001b;
    --grey: #7a7a7a;
    --text: #555555;
    --divider: #c9c9c9;
  }
  * { box-sizing: border-box; margin: 0; padding: 0; }
  html, body { width: 1200px; height: 960px; overflow: hidden; }
  body {
    background: var(--backdrop);
    font-family: "Roboto", Arial, sans-serif;
    position: relative;
  }
  .card {
    position: absolute;
    width: 600px;
    height: 342px;
    background: var(--card);
    box-shadow: 0 3px 8px rgba(0,0,0,0.25);
  }
  .card--front { left: 314px; top: 113px; }
  .card--back { left: 311px; top: 472px; }

  .band { position: absolute; left: 0; width: 100%; height: 25px; background: var(--red); }
  .band--top { top: 0; }
  .band--bottom { bottom: 0; }

  .brand {
    position: absolute;
    display: flex;
    align-items: center;
    gap: 10px;
    transform: translate(-50%, -50%);
    white-space: nowrap;
  }
  .brand__mark { background: var(--red); flex: none; }
  .brand__name { color: var(--grey); font-weight: 700; line-height: 1; letter-spacing: 0.5px; }

  .card--front .brand { left: 184px; top: 162px; }
  .card--front .brand__mark { width: 12px; height: 12px; }
  .card--front .brand__name { font-size: 40px; }

  .divider {
    position: absolute;
    left: 337px; top: 102px;
    width: 1px; height: 118px;
    background: var(--divider);
  }

  .contact { position: absolute; left: 361px; top: 104px; }
  .contact__name { color: var(--red); font-weight: 500; font-size: 22px; line-height: 1.1; }
  .contact__title { color: var(--grey); font-size: 15px; margin-top: 3px; }
  .contact__list { list-style: none; margin-top: 10px; }
  .contact__item {
    display: flex; align-items: center; gap: 9px;
    color: var(--text); font-size: 14px; line-height: 19px;
  }
  .contact__icon { width: 13px; height: 13px; fill: var(--red); flex: none; }

  .card--back .brand { left: 296px; top: 163px; }
  .card--back .brand__mark { width: 16px; height: 16px; }
  .card--back .brand__name { font-size: 54px; }

  .services {
    position: absolute; left: 0; top: 256px; width: 100%;
    text-align: center; color: var(--text); font-size: 14px; line-height: 18px;
  }
  .services .dot { color: var(--red); padding: 0 2px; }
</style>
</head>
<body>
  <section class="card card--front">
    <div class="band band--top"></div>
    <div class="brand">
      <span class="brand__mark"></span>
      <span class="brand__name">IRONSPAN</span>
    </div>
    <div class="divider"></div>
    <div class="contact">
      <p class="contact__name">DANIEL HARLOW</p>
      <p class="contact__title">CEO/FOUNDER</p>
      <ul class="contact__list">
        <li class="contact__item">
          <svg class="contact__icon" viewBox="0 0 16 16"><path d="M3.2 1l2.6 3.2-1.5 1.9c.9 2 2.6 3.8 4.6 4.7l1.9-1.5L14 11.9l-1.3 2.6C7 14.3 1.7 9 1.6 2.3z"/></svg>
          604 555 0187
        </li>
        <li class="contact__item">
          <svg class="contact__icon" viewBox="0 0 16 16"><path d="M1 3.5h14v1L8 9 1 4.5z"/><path d="M1 6l7 4.5L15 6v6.5H1z"/></svg>
          info@ironspan.com
        </li>
        <li class="contact__item">
          <svg class="contact__icon" viewBox="0 0 16 16"><circle cx="8" cy="8" r="7"/><path d="M5 4c1 1 2 1 2 2.5S5 8 5.5 9.5 8 10 8 12" stroke="#f7f7f7" stroke-width="1.3" fill="none"/></svg>
          www.ironspan.com
        </li>
      </ul>
    </div>
    <div class="band band--bottom"></div>
  </section>

  <section class="card card--back">
    <div class="brand">
      <span class="brand__mark"></span>
      <span class="brand__name">IRONSPAN</span>
    </div>
    <div class="services">
      <p>Refining <span class="dot">•</span> Rail <span class="dot">•</span> Infrastructure <span class="dot">•</span> Mining</p>
      <p>Energy <span class="dot">•</span> Calgary <span class="dot">•</span> Edmonton <span class="dot">•</span> Fort McMurray</p>
      <p>Revelstoke <span class="dot">•</span> Vancouver</p>
    </div>
  </section>
</body>
</html>
```